Calvanto Group Real Estate Company business cards

New business card design, we are generally happy with the basic layout of the existing front of business card, (feel free to change) but require a head shot photo on the back side.

http://www.calvanto.com.au/

Attached logos, and existing business card

------------------------------

Target Market(s)

Real estate

Industry/Entity Type

Real Estate

Contact Information for Business Card

Standard size double sided

Font styles to use
Other font styles liked:
• Futura

Requirements
Must have
• Photo head shot on the back side
Nice to have
• yes
Should not have
• No

```html
<!DOCTYPE html>
<html lang="en">
<head>
<meta charset="utf-8">
<title>Calvanto Group – Business Cards</title>
<link href="https://fonts.googleapis.com/css2?family=Jost:wght@400;500;600;700;800&display=swap" rel="stylesheet">
<style>
  :root {
    --backdrop: #2b2b2d;
    --card-black: #050505;
    --brand-orange: #f39a1e;
    --brand-purple: #3f2a84;
    --text-white: #ffffff;
    --photo-light: #e9ebee;
    --photo-dark: #2a3350;
  }
  html, body {
    margin: 0;
    padding: 0;
    width: 1200px;
    height: 900px;
    overflow: hidden;
    background: var(--backdrop);
    font-family: "Jost", "Futura", sans-serif;
  }
  .canvas {
    position: relative;
    width: 1200px;
    height: 900px;
  }
  .card {
    position: absolute;
    width: 580px;
    height: 354px;
    background: var(--card-black);
    border-radius: 20px;
    overflow: hidden;
    box-shadow: 0 10px 30px rgba(0,0,0,0.45);
    color: var(--text-white);
  }
  .card--front { left: 90px; top: 90px; }
  .card--back { left: 530px; top: 460px; }

  .card-band {
    position: absolute;
    inset: 0;
    width: 100%;
    height: 100%;
  }

  .wordmark {
    position: absolute;
    color: var(--text-white);
    font-weight: 400;
    line-height: 1;
  }
  .wordmark__name { display: block; letter-spacing: -1px; }
  .wordmark__group {
    display: block;
    text-align: right;
    text-transform: uppercase;
  }

  .card--front .wordmark {
    left: 0; right: 0;
    top: 58px;
    margin: 0 auto;
    width: 360px;
  }
  .card--front .wordmark__name { font-size: 96px; }
  .card--front .wordmark__group {
    font-size: 14px;
    letter-spacing: 9px;
    margin-top: 2px;
    padding-right: 6px;
  }

  .services {
    position: absolute;
    top: 210px;
    left: 0; right: 0;
    margin: 0;
    text-align: center;
    font-size: 21px;
    font-weight: 500;
    letter-spacing: 2px;
  }
  .services__divider { color: var(--brand-orange); margin: 0 6px; }

  .band-text {
    font-family: "Jost", "Futura", sans-serif;
    fill: var(--text-white);
  }
  .band-text__accent { fill: var(--brand-orange); }

  .card--back .wordmark { left: 40px; top: 92px; width: 250px; }
  .card--back .wordmark__name { font-size: 66px; }
  .card--back .wordmark__group {
    font-size: 10px;
    letter-spacing: 7px;
    margin-top: 1px;
    padding-right: 4px;
  }

  .headshot {
    position: absolute;
    left: 318px;
    top: 32px;
    width: 220px;
    height: 220px;
    border-radius: 50%;
    background: radial-gradient(circle at 50% 45%, var(--photo-light) 0%, #c9ccd3 45%, var(--photo-dark) 78%, #0b0b0b 100%);
  }

  .contact-tab {
    position: absolute;
    left: 0;
    top: 228px;
    width: 14px;
    height: 104px;
    background: var(--brand-purple);
    border-radius: 0 12px 12px 0;
  }

  .contact {
    position: absolute;
    left: 36px;
    top: 178px;
    line-height: 1;
  }
  .contact__name {
    font-size: 27px;
    font-weight: 800;
    letter-spacing: 0.5px;
    margin: 0;
  }
  .contact__role {
    font-size: 13px;
    font-weight: 500;
    color: var(--brand-orange);
    margin: 4px 0 6px;
    letter-spacing: 0.5px;
  }
  .contact__abn {
    font-size: 15px;
    margin: 0 0 8px;
  }
  .contact__label { color: var(--brand-orange); }
  .contact__list {
    list-style: none;
    margin: 0;
    padding: 0;
    font-size: 13.5px;
  }
  .contact__item {
    display: flex;
    align-items: center;
    gap: 8px;
    margin-bottom: 5px;
  }
  .contact__icon { width: 12px; height: 12px; flex: none; }
  .contact__item--phone { font-size: 15px; }
</style>
</head>
<body>
<main class="canvas">

  <section class="card card--front" aria-label="Business card front">
    <svg class="card-band" viewBox="0 0 580 354">
      <defs>
        <path id="front-text-curve" d="M0,374 Q300,354 580,252"/>
      </defs>
      <path d="M0,354 L0,352 Q300,338 580,230 L580,354 Z" fill="var(--brand-purple)"/>
      <path d="M-4,348 Q300,332 584,222" fill="none" stroke="var(--brand-orange)" stroke-width="4"/>
      <text class="band-text" font-size="19">
        <textPath href="#front-text-curve" startOffset="50%" text-anchor="middle"><tspan class="band-text__accent">www.</tspan><tspan font-weight="700">calvanto.com</tspan><tspan class="band-text__accent">.au</tspan></textPath>
      </text>
    </svg>

    <div class="wordmark">
      <span class="wordmark__name">calvanto</span>
      <span class="wordmark__group">group</span>
    </div>

    <p class="services">Buy<span class="services__divider">|</span>Sell<span class="services__divider">|</span>Rent</p>
  </section>

  <section class="card card--back" aria-label="Business card back">
    <div class="headshot" role="img" aria-label="Head shot photo of the director in a suit"></div>

    <svg class="card-band" viewBox="0 0 580 354">
      <defs>
        <path id="back-text-curve" d="M90,392 Q340,368 580,236"/>
      </defs>
      <path d="M70,354 Q330,330 580,204 L580,354 Z" fill="var(--brand-purple)"/>
      <path d="M62,356 Q330,322 584,194" fill="none" stroke="var(--brand-orange)" stroke-width="4"/>
      <text class="band-text" font-size="20">
        <textPath href="#back-text-curve" startOffset="66%" text-anchor="middle">your next home starts here</textPath>
      </text>
    </svg>

    <div class="wordmark">
      <span class="wordmark__name">calvanto</span>
      <span class="wordmark__group">group</span>
    </div>

    <div class="contact-tab"></div>

    <div class="contact">
      <h2 class="contact__name">DANIEL TRAN</h2>
      <p class="contact__role">DIRECTOR</p>
      <p class="contact__abn"><span class="contact__label">ABN:</span> 41 208 635 917</p>
      <ul class="contact__list">
        <li class="contact__item contact__item--phone">
          <svg class="contact__icon" viewBox="0 0 12 12"><rect x="2.5" y="0.5" width="7" height="11" rx="1.5" fill="none" stroke="var(--brand-orange)" stroke-width="1.2"/><circle cx="6" cy="9.3" r="0.8" fill="var(--brand-orange)"/></svg>
          0412 586 304
        </li>
        <li class="contact__item">
          <svg class="contact__icon" viewBox="0 0 12 12"><rect x="0.6" y="2" width="10.8" height="8" rx="1" fill="none" stroke="var(--brand-orange)" stroke-width="1.2"/><path d="M1,2.5 L6,6.5 L11,2.5" fill="none" stroke="var(--brand-orange)" stroke-width="1.2"/></svg>
          daniel.tran@calvanto.com.au
        </li>
        <li class="contact__item">
          <svg class="contact__icon" viewBox="0 0 12 12"><circle cx="6" cy="6" r="5.3" fill="var(--brand-orange)"/><path d="M0.8,6 H11.2 M6,0.8 C3.5,3.5 3.5,8.5 6,11.2 M6,0.8 C8.5,3.5 8.5,8.5 6,11.2" fill="none" stroke="var(--card-black)" stroke-width="0.8"/></svg>
          www.calvanto.com.au
        </li>
      </ul>
    </div>
  </section>

</main>
</body>
</html>
```